Website Design for recruiting company

We need a homepage mockup for a recruiting company focused on the legal industry. Use your creative talent to come up with something visually appeal and professional for this web-site.

We'd really like to see the maze from the logo incorporated into the design somehow. Please use the website mockup provided as inspiration for this project. We really like the layout and photos!

Target Market(s)

lawyers

Industry/Entity Type

Legal

Number of Pages Required

1 page

Font styles to use
Sans Serif

```html
<!DOCTYPE html>
<html lang="en">
<head>
<meta charset="utf-8">
<title>Harbor Point Legal Search</title>
<link href="https://fonts.googleapis.com/css2?family=Lato:wght@300;400;700;900&display=swap" rel="stylesheet">
<style>
:root{
  --plum:#5b4558;
  --plum-dark:#4a3648;
  --ink:#2f2f33;
  --muted:#6d6d72;
  --grey-band:#e9e9ea;
  --white:#ffffff;
  --hedge-dark:#2c4220;
  --hedge-mid:#557436;
  --hedge-light:#8fa65c;
  --navy-1:#1b2a40;
  --navy-2:#55697f;
}
*{box-sizing:border-box;margin:0;padding:0}
html,body{width:1200px;height:2716px;overflow:hidden}
body{font-family:'Lato',sans-serif;color:var(--ink);background:var(--white);position:relative}
a{color:inherit;text-decoration:none}

.hero{position:absolute;left:0;top:0;width:1200px;height:690px;overflow:hidden}
.hero-photo{position:absolute;inset:0;background:
  radial-gradient(ellipse 520px 300px at 78% 30%,rgba(150,175,100,.75),transparent 70%),
  radial-gradient(ellipse 600px 260px at 25% 85%,rgba(120,150,80,.6),transparent 70%),
  radial-gradient(ellipse 420px 220px at 55% 55%,rgba(170,185,120,.45),transparent 70%),
  linear-gradient(160deg,var(--hedge-mid),var(--hedge-dark) 55%,var(--hedge-mid))}
.hero-shade{position:absolute;inset:0;background:linear-gradient(90deg,rgba(0,0,0,.45),rgba(0,0,0,.15) 55%,rgba(0,0,0,.05)),linear-gradient(180deg,rgba(0,0,0,.35),transparent 25%)}
.site-header{position:absolute;left:0;top:0;width:1200px;height:100px;display:flex;align-items:center;padding:0 60px}
.brand{display:flex;align-items:center;gap:14px;color:var(--white);font-size:19px;font-weight:400}
.brand-mark{width:56px;height:56px;border-radius:50%;background:rgba(255,255,255,.85)}
.main-nav{margin-left:auto;display:flex;gap:34px}
.main-nav a{color:var(--white);font-size:14px;font-weight:700;letter-spacing:.5px;padding-bottom:6px}
.main-nav a.active{border-bottom:2px solid var(--white)}
.hero-copy{position:absolute;left:150px;top:230px;width:560px;color:var(--white)}
.hero-copy h1{font-size:46px;line-height:56px;font-weight:900}
.hero-copy p{margin-top:16px;font-size:15px;line-height:22px;opacity:.9;width:430px}
.btn{display:inline-flex;align-items:center;gap:10px;font-size:14px;font-weight:700;letter-spacing:1px}
.btn-dark{background:var(--plum);color:var(--white);padding:14px 28px}
.btn-outline{border:1.5px solid var(--ink);padding:13px 26px}
.btn-light{border:1.5px solid var(--white);color:var(--white);padding:12px 28px}
.hero-copy .btn{margin-top:36px}
.slider-dots{position:absolute;left:1104px;top:296px;display:flex;flex-direction:column;gap:16px}
.slider-dots span{width:12px;height:12px;border-radius:50%;background:var(--white)}
.slider-dots span.current{background:transparent;border:2px solid var(--white)}

.about{position:absolute;left:0;top:690px;width:1200px;height:532px}
.about-art{position:absolute;left:140px;top:80px;width:330px;height:330px;border-radius:50%;background:
  radial-gradient(circle at 50% 50%,#f1e3bf 0,#d9c9a4 14%,transparent 30%),
  radial-gradient(circle at 30% 30%,#9fb7d8,transparent 45%),
  radial-gradient(circle at 75% 70%,#3d5a93,transparent 50%),
  conic-gradient(from 30deg,#6f8fc4,#c9d6ea,#42598e,#a7bcdc,#2f4272,#8aa4cf,#6f8fc4)}
.about-text{position:absolute;left:548px;top:108px;width:530px}
.about-text h2{font-size:36px;font-weight:400;letter-spacing:1px}
.about-text p{margin-top:20px;font-size:14.5px;line-height:26px;color:var(--muted)}
.about-text .btn{margin-top:24px}

.news{position:absolute;left:0;top:1222px;width:1200px;height:593px;background:var(--grey-band)}
.news-badge{position:absolute;left:574px;top:-28px;width:52px;height:52px;border-radius:50%;background:var(--plum);border:5px solid var(--white)}
.news h2{position:absolute;left:0;top:44px;width:1200px;text-align:center;font-size:30px;font-weight:400;letter-spacing:1px}
.cards{position:absolute;left:40px;top:88px;display:flex;gap:14px}
.card{width:217px;height:345px;background:var(--white);position:relative;box-shadow:0 2px 6px rgba(0,0,0,.08)}
.card-photo{height:145px}
.photo-a{background:linear-gradient(135deg,#dfe6ee,#8b98a8 55%,#3f4d60)}
.photo-b{background:linear-gradient(135deg,#c7ced6,#6f7d8e 50%,#2e3a4b)}
.photo-c{background:linear-gradient(135deg,#e4e8ee,#9aa8ba 50%,#51627a)}
.photo-d{background:linear-gradient(135deg,#d8d3cb,#8a8a8f 50%,#3a3d48)}
.photo-e{background:linear-gradient(135deg,#f0ece6,#b8b1a8 50%,#5c5860)}
.card-icon{position:absolute;left:88px;top:126px;width:40px;height:40px;border-radius:50%;background:var(--white);border:2px solid var(--plum)}
.card h3{margin:40px 16px 0;font-size:14px;line-height:19px;font-weight:700}
.card p{margin:10px 16px 0;font-size:11.5px;line-height:17px;color:var(--muted)}
.card .more{position:absolute;left:16px;bottom:18px;font-size:11px;font-weight:700}
.news .btn{position:absolute;left:492px;top:478px}

.employers{position:absolute;left:0;top:1815px;width:1200px;height:525px;overflow:hidden}
.employers-photo{position:absolute;inset:0;background:
  radial-gradient(ellipse 260px 230px at 34% 40%,rgba(205,215,228,.55),transparent 70%),
  radial-gradient(ellipse 240px 300px at 42% 80%,rgba(140,158,182,.55),transparent 70%),
  radial-gradient(ellipse 200px 320px at 8% 60%,rgba(95,112,135,.8),transparent 70%),
  linear-gradient(90deg,var(--navy-2),#3b4e66 45%,var(--navy-1) 75%)}
.employers-shade{position:absolute;inset:0;background:linear-gradient(90deg,transparent 45%,rgba(20,32,50,.55) 65%,rgba(20,32,50,.7))}
.employers-text{position:absolute;left:630px;top:250px;width:440px;color:var(--white)}
.employers-text h2{font-size:26px;font-weight:400;letter-spacing:1px}
.employers-text p{margin-top:14px;font-size:14.5px;line-height:22px;opacity:.9}
.employers-text h3{margin-top:20px;font-size:17px;font-weight:700;letter-spacing:1px}
.employers-text .btn{margin-top:18px}

.site-footer{position:absolute;left:0;top:2340px;width:1200px;height:376px;background:var(--plum);color:var(--white)}
.footer-col{position:absolute;top:65px}
.footer-col h4{font-size:16px;font-weight:700;letter-spacing:1px;margin-bottom:16px}
.footer-col li{list-style:none;font-size:13px;line-height:26px;opacity:.85}
.contact-line{display:flex;align-items:center;gap:10px;font-size:13px;line-height:26px}
.socials{display:flex;gap:8px;margin-top:12px}
.socials span{width:30px;height:30px;border-radius:50%;border:1.5px solid var(--white)}
.footer-rule{position:absolute;left:155px;top:300px;width:890px;border-top:1px solid rgba(255,255,255,.3)}
.copyright{position:absolute;left:0;top:322px;width:1200px;text-align:center;font-size:12px;opacity:.75}
</style>
</head>
<body>

<section class="hero">
  <div class="hero-photo" role="img" aria-label="Aerial view of a green hedge maze"></div>
  <div class="hero-shade"></div>
  <header class="site-header">
    <a class="brand" href="#"><span class="brand-mark"></span>Harbor Point Legal Search</a>
    <nav class="main-nav">
      <a class="active" href="#">ABOUT US</a>
      <a href="#">WHAT'S NEW</a>
      <a href="#">FOR EMPLOYERS</a>
      <a href="#">IN HOUSE</a>
      <a href="#">CONTACT US</a>
    </nav>
  </header>
  <div class="hero-copy">
    <h1>Start Here, Let Our Experience Guide You</h1>
    <p>Connecting talented attorneys with firms that value them, across every practice area.</p>
    <a class="btn btn-dark" href="#">LEARN MORE
      <svg width="18" height="10" viewBox="0 0 18 10"><path d="M0 5h16M12 1l4 4-4 4" stroke="currentColor" stroke-width="1.6" fill="none"/></svg></a>
  </div>
  <div class="slider-dots"><span></span><span class="current"></span><span></span></div>
</section>

<section class="about">
  <div class="about-art" role="img" aria-label="Circular maze illustration with a figure at its centre"></div>
  <div class="about-text">
    <h2>ABOUT US</h2>
    <p>Harbor Point Legal Search focuses on the permanent placement of attorneys with law firms and corporations in the New England area. Founded in 1982, Harbor Point Legal Search is the oldest attorney search firm in New England, and is ranked the number one legal recruiter in New England in the most recent survey conducted by The Counsel Review.</p>
    <a class="btn btn-outline" href="#">LEARN MORE
      <svg width="18" height="10" viewBox="0 0 18 10"><path d="M0 5h16M12 1l4 4-4 4" stroke="currentColor" stroke-width="1.6" fill="none"/></svg></a>
  </div>
</section>

<section class="news">
  <span class="news-badge"></span>
  <h2>WHAT'S NEW</h2>
  <div class="cards">
    <article class="card"><div class="card-photo photo-a" role="img" aria-label="Colleagues in a meeting"></div><span class="card-icon"></span>
      <h3>Praesent sit amet est in dictum eu dictum</h3><p>Etiam eleifend massa vitae pro placerat semper mauris.</p><a class="more" href="#">CLICK HERE →</a></article>
    <article class="card"><div class="card-photo photo-b" role="img" aria-label="Team discussing documents"></div><span class="card-icon"></span>
      <h3>Aliquam nec erat at purus interdum</h3><p>Etiam eleifend massa vitae pro placerat semper mauris.</p><a class="more" href="#">CLICK HERE →</a></article>
    <article class="card"><div class="card-photo photo-c" role="img" aria-label="Professionals shaking hands"></div><span class="card-icon"></span>
      <h3>Curabitur vel mi sit amet magna malesuada</h3><p>Etiam eleifend massa vitae pro placerat semper mauris.</p><a class="more" href="#">CLICK HERE →</a></article>
    <article class="card"><div class="card-photo photo-d" role="img" aria-label="Lawyers reviewing a contract"></div><span class="card-icon"></span>
      <h3>Mauris neque metus malesuada ultrici</h3><p>Etiam eleifend massa vitae pro placerat semper mauris.</p><a class="more" href="#">CLICK HERE →</a></article>
    <article class="card"><div class="card-photo photo-e" role="img" aria-label="Candidate at an interview"></div><span class="card-icon"></span>
      <h3>Praesent sit amet est in dictum eu dictum</h3><p>Etiam eleifend massa vitae pro placerat semper mauris.</p><a class="more" href="#">CLICK HERE →</a></article>
  </div>
  <a class="btn btn-dark" href="#">SEARCH JOBS
    <svg width="18" height="10" viewBox="0 0 18 10"><path d="M0 5h16M12 1l4 4-4 4" stroke="currentColor" stroke-width="1.6" fill="none"/></svg></a>
</section>

<section class="employers">
  <div class="employers-photo" role="img" aria-label="Business people in conversation at an office table"></div>
  <div class="employers-shade"></div>
  <div class="employers-text">
    <h2>FOR EMPLOYERS</h2>
    <p>Our unparalleled recruiting industry and legal experience have generated an extensive network of contacts throughout the legal community.</p>
    <h3>FIND THE RIGHT CANDIDATE</h3>
    <a class="btn btn-light" href="#">START HERE
      <svg width="18" height="10" viewBox="0 0 18 10"><path d="M0 5h16M12 1l4 4-4 4" stroke="currentColor" stroke-width="1.6" fill="none"/></svg></a>
  </div>
</section>

<footer class="site-footer">
  <div class="footer-col" style="left:160px"><h4>QUICK LINKS</h4><ul><li>Law Firms</li><li>Associate</li><li>Partner</li><li>Other</li></ul></div>
  <div class="footer-col" style="left:405px"><h4>RESOURCES</h4><ul><li>Regional</li><li>What's New</li><li>About Us</li><li>For Employers</li></ul></div>
  <div class="footer-col" style="left:645px"><h4>LINKS</h4><ul><li>Law Firms</li><li>Submit Resume</li><li>Contact Us</li></ul></div>
  <div class="footer-col" style="left:840px"><h4>CONTACT US</h4>
    <div class="contact-line"><svg width="14" height="14" viewBox="0 0 14 14"><path d="M3 1l2 3-1.5 1.5a8 8 0 0 0 5 5L10 9l3 2-1 2.5C6 13 1 8 1 2z" fill="currentColor"/></svg>(555) 014-2280</div>
    <div class="contact-line"><svg width="14" height="12" viewBox="0 0 14 12"><rect x="1" y="1" width="12" height="10" fill="none" stroke="currentColor" stroke-width="1.4"/><path d="M1 1l6 5 6-5" fill="none" stroke="currentColor" stroke-width="1.4"/></svg>info@harborpointlegal.com</div>
    <div class="socials"><span></span><span></span><span></span><span></span></div>
  </div>
  <div class="footer-rule"></div>
  <p class="copyright">© 2020 Company Name. All Rights Reserved.</p>
</footer>

</body>
</html>
```